Law Firm Web Design Project

I need a website design for my law firm. I have attached to this description the URL of a website I liked with a description of the elements of that website that appeal to me.

I am also attaching my law firm's logo, so you can review that design when you create the website design.

Reference Site: www.harborfieldcounsel-example.com

What we like about this site:
• The different layers
• Subtle designs, textures, curves
• 3 dimensional
• Floating effect
• Simple logo that stands out (we are providing logo)
• Prominent phone number
• Location of Areas of Practice
oDivorce, Legal Separation, Paternity, Spousal Maintenance, Child Custody, Child Support, Protective Orders, Community Property, Business Evaluations
• The limited amount of links across the top
o Home, Meet Our Attorney, FAQ, Contact Us
• Request A Consultation click through
• Right side bar with the moving icons
• Badges

Other Tips:
• We don’t want the website to be dark. The logo can standout and the website can have its own colors and flow.
• We would like there to be a “call to action” or way to get in touch on every page and every page view
• We would like a place for credit card icons at the bottom of the page
• Strong, yet elegant
• Finally, just use the website provided as a guide. Explore different colors, textures, shapes, shadows etc.
Updates

I would prefer the website have colors that are complementary to my logo and that are strong and elegant.  I like black, gold, amber, and tan colors.  Black should be used sparingly as an accent only, since I don't want the website to be too dark.

Please review the website I provided as an example in my project description.  I really like the three dimensional aspects of that website (web page floating on top of a background and the logo in the upper left floating on top of the web page).  I also like the use of "swirling" on the background and the webpage.  I hope this additional information is helpful.

Requirements
Must have
• I need a place to insert "client testimonials", a place to insert four logos of awards the law firm has received, a place for people to fill out a form to contact the law firm via email, and a place for people to click to review articles I have written.

```html
<!DOCTYPE html>
<html lang="en">
<head>
<meta charset="utf-8">
<title>Marlowe Law</title>
<link rel="stylesheet" href="https://fonts.googleapis.com/css2?family=Ubuntu:wght@400;500;700&family=Arimo:wght@400;700&family=PT+Serif:ital@1&family=Open+Sans:wght@300;400&family=Arvo:wght@700&display=swap">
<style>
:root{
  --gold-bg:#9c8230;
  --gold-deep:#6e5414;
  --page:#bda755;
  --cream:#ede3bf;
  --header:#f3f1eb;
  --title:#c98a0c;
  --orange:#e5520f;
  --nav:#8b7a45;
  --footer-gold:#c9a53a;
}
*{box-sizing:border-box;margin:0;padding:0}
html,body{width:973px;height:1200px;overflow:hidden}
body{background:radial-gradient(ellipse at 60% 30%,#c8ad55 0%,#a58a33 45%,#5e4a17 85%,#2f2509 100%);font-family:"Arimo",sans-serif;position:relative}
.page{position:absolute;left:82px;top:0;width:809px;height:1135px;background:linear-gradient(#c2ab58,#b09742);box-shadow:0 0 18px rgba(0,0,0,.45)}

.header{position:absolute;left:0;top:0;width:809px;height:150px;background:var(--header)}
.brand{position:absolute;left:12px;top:28px;display:flex;align-items:center;gap:12px}
.brand-mark{width:50px;height:50px;background:#1d1a12}
.brand-name{font-family:"Ubuntu",sans-serif;font-weight:500;font-size:30px;color:#7a6a3a;white-space:nowrap}
.nav a{position:absolute;top:24px;height:28px;line-height:28px;font-family:"Ubuntu",sans-serif;font-size:15px;color:var(--nav);text-decoration:none;white-space:nowrap}
.nav a.active{left:388px;width:64px;text-align:center;background:#7a6a2e;color:#fff}
.nav .n2{left:480px}.nav .n3{left:646px}.nav .n4{left:713px}
.call-label{position:absolute;right:22px;top:72px;font-size:11px;color:#333;font-weight:700}
.call-rule{position:absolute;right:22px;top:89px;width:180px;height:1px;background:#ccc}
.call-number{position:absolute;right:18px;top:92px;font-family:"Open Sans",sans-serif;font-weight:300;font-size:28px;line-height:30px;color:#777;white-space:nowrap}

.hero{position:absolute;left:0;top:0;z-index:2}
.hero-title{position:absolute;z-index:3;left:463px;top:150px;width:256px;text-align:center;line-height:1}
.hero-title .small{display:block;font-family:"Arvo",serif;font-weight:700;font-size:29px;color:#c99a28;letter-spacing:1px}
.hero-title .big{display:block;font-family:"Ubuntu",sans-serif;font-weight:700;font-size:38px;color:#fff;letter-spacing:1px;text-shadow:0 1px 3px rgba(0,0,0,.3)}
.slider-arrow{position:absolute;z-index:4;width:42px;height:35px;background:#222;box-shadow:0 2px 4px rgba(0,0,0,.5)}
.slider-arrow.prev{left:-11px;top:234px;border-radius:0 18px 18px 0}
.slider-arrow.next{left:778px;top:244px;border-radius:18px 0 0 18px}
.slider-arrow svg{position:absolute;left:14px;top:10px}

.card{position:absolute;top:370px;width:241px;height:325px;background:var(--cream);box-shadow:0 2px 6px rgba(0,0,0,.35)}
.card-title{position:absolute;z-index:5;left:16px;top:40px;font-family:"Ubuntu",sans-serif;font-weight:700;font-size:31px;color:var(--title);text-shadow:1px 1px 0 #fff,0 2px 3px rgba(0,0,0,.2)}
.card-sub{position:absolute;z-index:5;left:20px;top:77px;font-family:"Ubuntu",sans-serif;font-weight:500;font-size:12.5px;letter-spacing:1.5px;color:#777}
.company{left:25px}.awards{left:285px}.practice{left:543px}
.photo-team{position:absolute;left:11px;top:107px;width:220px;height:112px;background:#fff;padding:5px;box-shadow:0 1px 3px rgba(0,0,0,.2)}
.photo-team div{width:100%;height:100%;background:linear-gradient(90deg,#3c3c44,#8d8d95 50%,#2e3646)}
.card-text{position:absolute;left:13px;top:230px;width:218px;font-size:9.3px;line-height:13px;color:#555;text-align:justify;hyphens:auto}
.badge{position:absolute;background:#fff;box-shadow:0 1px 3px rgba(0,0,0,.25)}
.badge-main{left:14px;top:105px;width:206px;height:100px}
.badge-main .disc{position:absolute;left:9px;top:20px;width:58px;height:58px;border-radius:50%;background:#d8202a}
.badge-main .bar{position:absolute;left:72px;top:36px;width:126px;height:22px;background:#d8202a}
.badge-small{left:14px;top:216px;width:58px;height:94px}
.badge-small .shape{position:absolute;left:6px;top:6px;width:46px;height:82px;background:#1a5c9c;border-radius:3px}
.badge-wide{left:81px;top:216px;width:139px;height:94px}
.badge-wide .shape{position:absolute;left:12px;top:30px;width:115px;height:50px;background:#c7d2e6}
.practice-list{position:absolute;left:23px;top:100px;width:196px;list-style:none}
.practice-list li{display:flex;align-items:center;height:24.3px;border-bottom:1px solid #d5c89a;font-family:"Ubuntu",sans-serif;font-size:11.5px;color:#333;padding-left:4px;white-space:nowrap}
.practice-list li:last-child{border-bottom:none}
.practice-list svg{margin-right:8px;flex:none}

.testimonial{position:absolute;left:23px;top:718px;width:504px;height:192px;border:1px solid #c9b56a;padding:5px}
.testimonial-inner{width:100%;height:100%;background:linear-gradient(#8c7224,#86702a);border:1px solid #a9904a;position:relative;box-shadow:inset 0 0 6px rgba(0,0,0,.3)}
.section-title{position:absolute;font-family:"Ubuntu",sans-serif;font-weight:700;font-size:29px;color:#e8a412;white-space:nowrap;text-shadow:-1px -1px 0 #fff,1px -1px 0 #fff,-1px 1px 0 #fff,1px 1px 0 #fff,0 2px 4px rgba(0,0,0,.4)}
.testimonial .section-title{left:64px;top:8px}
.testimonial .dots{position:absolute;left:8px;right:8px;top:55px;border-top:2px dotted #b89f50}
.quote{position:absolute;left:8px;top:62px;width:468px;font-family:"PT Serif",serif;font-style:italic;font-size:15.2px;line-height:21px;color:#f5ecd0;text-align:justify;padding-left:19px}
.quote .mark{position:absolute;left:0;top:-4px;font-size:28px;color:#f5ecd0}
.quote .mark.end{position:static;font-size:24px;vertical-align:-6px}
.icon-bubble{position:absolute;left:10px;top:8px}

.email-box{position:absolute;left:542px;top:718px;width:242px;height:289px;background:#987e30;border:1px solid #c9b56a;box-shadow:inset 0 0 6px rgba(0,0,0,.2)}
.email-box .section-title{left:57px;top:10px;font-size:25px}
.email-box .rule{position:absolute;left:8px;right:8px;top:51px;border-top:1px solid #c5ad65}
.email-intro{position:absolute;left:11px;top:59px;width:222px;font-size:9.8px;line-height:14.5px;color:#fbf4de;letter-spacing:.4px;text-align:justify}
.field{position:absolute;left:10px;width:219px;height:21px;border:1px solid #b9a25b;background:#8b7128;font-size:9.8px;color:#efe3bb;padding:4px 8px;letter-spacing:.3px}
.field.area{height:55px}
.submit{position:absolute;left:166px;top:257px;width:61px;height:20px;background:#1c1c1c;color:#fff;font-size:10px;font-weight:700;border-radius:3px;text-align:center;line-height:20px}

.call-box{position:absolute;left:542px;top:1014px;width:242px;height:110px;background:#fff;border:2px solid #e8dcae;box-shadow:0 0 0 1px #9a8033}
.call-photo{position:absolute;left:2px;top:2px;width:72px;height:102px;background:linear-gradient(90deg,#e8e2d8,#f08a40 60%,#e8e2d8)}
.call-big{position:absolute;left:89px;top:4px;font-weight:700;font-size:38px;color:var(--orange);line-height:1}
.call-sub{position:absolute;left:96px;top:42px;font-weight:700;font-size:15px;color:#222;letter-spacing:1px}
.call-copy{position:absolute;left:77px;top:60px;width:156px;font-size:9.8px;line-height:13px;color:#333}

.articles .section-title{left:83px;top:940px}
.articles .icon{position:absolute;left:28px;top:939px}
.articles .rule{position:absolute;left:25px;width:493px;top:986px;border-top:1px solid #8d7634;box-shadow:0 1px 0 #d4c27f}
.article{position:absolute;left:53px;width:460px;font-size:9.5px;line-height:13px;color:#fff;letter-spacing:.35px}
.article::before{content:"";position:absolute;left:-11px;top:3px;border-left:4px solid #5a4712;border-top:3px solid transparent;border-bottom:3px solid transparent}
.view-all{position:absolute;left:452px;top:1106px;font-size:9.5px;font-weight:700;color:#222}

.footer{position:absolute;left:82px;top:1135px;width:809px;height:65px;background:linear-gradient(#2c2510,#1a160a)}
.footer-brand{position:absolute;left:18px;top:15px;display:flex;align-items:center;gap:8px;font-family:"Ubuntu",sans-serif;font-weight:500;font-size:14px;color:var(--footer-gold)}
.footer-brand .sq{width:30px;height:30px;background:var(--footer-gold)}
.footer-nav{position:absolute;left:246px;top:21px;font-size:10px;color:var(--footer-gold);letter-spacing:.3px;width:300px;text-align:center;line-height:13px}
.footer-nav .copy{display:block;color:#b09a5a}
.footer-phone{position:absolute;right:6px;top:12px;display:flex;align-items:center;gap:6px;font-family:"Open Sans",sans-serif;font-weight:300;font-size:28px;color:#9a8f72}
</style>
</head>
<body>
<div class="page">
  <header class="header">
    <div class="brand"><span class="brand-mark"></span><span class="brand-name">Marlowe Law</span></div>
    <nav class="nav">
      <a class="active" href="#">Home</a><a class="n2" href="#">Meet Our Attorney</a><a class="n3" href="#">FAQ</a><a class="n4" href="#">Contact Us</a>
    </nav>
    <div class="call-label">Call Us Today</div>
    <div class="call-rule"></div>
    <div class="call-number">123 456 7890</div>
  </header>

  <section class="company card">
    <h2 class="card-title">Company</h2>
    <p class="card-sub">WELCOME MESSAGE</p>
    <div class="photo-team"><div role="img" aria-label="Photo of the legal team in business attire"></div></div>
    <p class="card-text">Quisque rhoncus, turpis sed vehicula adipiscing, urna massa bibendum erat, vel rhoncus eros sapien sed tellus. Nam vehicula nisi sed sem vulputate nec posuere enim venenatis. Sed a arcu sed nisi porttitor lacinia vel eget magna. ..</p>
  </section>

  <section class="awards card">
    <h2 class="card-title">Awards</h2>
    <p class="card-sub">RECIEVED FROM</p>
    <div class="badge badge-main" role="img" aria-label="Peer review rating badge for Daniel R. Marlowe"><span class="disc"></span><span class="bar"></span></div>
    <div class="badge badge-small" role="img" aria-label="Accredited business badge"><span class="shape"></span></div>
    <div class="badge badge-wide" role="img" aria-label="Top solo practitioner award badge"><span class="shape"></span></div>
  </section>

  <section class="practice card">
    <h2 class="card-title">Practice</h2>
    <p class="card-sub">LOCATION OF AREAS</p>
    <ul class="practice-list">
      <li><svg width="16" height="16" viewBox="0 0 16 16"><circle cx="8" cy="8" r="7" fill="#fff" stroke="#666" stroke-width="1.5"/><path d="M5 8h6M8 5l3 3-3 3" stroke="#555" stroke-width="1.6" fill="none"/></svg>Divorce</li>
      <li><svg width="16" height="16" viewBox="0 0 16 16"><circle cx="8" cy="8" r="7" fill="#fff" stroke="#666" stroke-width="1.5"/><path d="M5 8h6M8 5l3 3-3 3" stroke="#555" stroke-width="1.6" fill="none"/></svg>Legal Separation</li>
      <li><svg width="16" height="16" viewBox="0 0 16 16"><circle cx="8" cy="8" r="7" fill="#fff" stroke="#666" stroke-width="1.5"/><path d="M5 8h6M8 5l3 3-3 3" stroke="#555" stroke-width="1.6" fill="none"/></svg>Paternity</li>
      <li><svg width="16" height="16" viewBox="0 0 16 16"><circle cx="8" cy="8" r="7" fill="#fff" stroke="#666" stroke-width="1.5"/><path d="M5 8h6M8 5l3 3-3 3" stroke="#555" stroke-width="1.6" fill="none"/></svg>Spousal Maintenance</li>
      <li><svg width="16" height="16" viewBox="0 0 16 16"><circle cx="8" cy="8" r="7" fill="#fff" stroke="#666" stroke-width="1.5"/><path d="M5 8h6M8 5l3 3-3 3" stroke="#555" stroke-width="1.6" fill="none"/></svg>Child Custody</li>
      <li><svg width="16" height="16" viewBox="0 0 16 16"><circle cx="8" cy="8" r="7" fill="#fff" stroke="#666" stroke-width="1.5"/><path d="M5 8h6M8 5l3 3-3 3" stroke="#555" stroke-width="1.6" fill="none"/></svg>Child Support</li>
      <li><svg width="16" height="16" viewBox="0 0 16 16"><circle cx="8" cy="8" r="7" fill="#fff" stroke="#666" stroke-width="1.5"/><path d="M5 8h6M8 5l3 3-3 3" stroke="#555" stroke-width="1.6" fill="none"/></svg>Protective Orders</li>
      <li><svg width="16" height="16" viewBox="0 0 16 16"><circle cx="8" cy="8" r="7" fill="#fff" stroke="#666" stroke-width="1.5"/><path d="M5 8h6M8 5l3 3-3 3" stroke="#555" stroke-width="1.6" fill="none"/></svg>Community Property Business</li>
      <li><svg width="16" height="16" viewBox="0 0 16 16"><circle cx="8" cy="8" r="7" fill="#fff" stroke="#666" stroke-width="1.5"/><path d="M5 8h6M8 5l3 3-3 3" stroke="#555" stroke-width="1.6" fill="none"/></svg>Evaluations</li>
    </ul>
  </section>

  <svg class="hero" width="809" height="440" viewBox="0 0 809 440">
    <defs>
      <linearGradient id="heroPhoto" x1="0" y1="0" x2="1" y2="0">
        <stop offset="0" stop-color="#b9b2a2"/>
        <stop offset=".35" stop-color="#7a6a5a"/>
        <stop offset=".7" stop-color="#8f8a68"/>
        <stop offset="1" stop-color="#6d7a46"/>
      </linearGradient>
      <linearGradient id="band" x1="0" y1="0" x2="1" y2="0">
        <stop offset="0" stop-color="#f3dc8f"/>
        <stop offset=".4" stop-color="#c8a24a"/>
        <stop offset="1" stop-color="#6b4a08"/>
      </linearGradient>
      <linearGradient id="lowBand" x1="0" y1="0" x2="1" y2="0">
        <stop offset="0" stop-color="#5a3c05"/>
        <stop offset=".5" stop-color="#7d5a12"/>
        <stop offset="1" stop-color="#a47d26"/>
      </linearGradient>
    </defs>
    <path fill="#f6ecc4" d="M0 118 C120 106 220 72 330 72 C460 72 560 112 650 116 L650 122 C560 118 460 78 330 78 C220 78 120 112 0 126 Z"/>
    <path role="img" aria-label="Photo of a thoughtful woman with a man in the background, outdoors" fill="url(#heroPhoto)" d="M0 142 C120 132 220 96 330 96 C460 96 560 137 650 142 L809 148 V412 C760 395 700 362 600 360 C500 360 430 398 330 398 C230 398 120 352 0 356 Z"/>
    <path fill="url(#band)" d="M0 126 C120 112 220 78 330 78 C460 78 560 118 650 122 L809 124 V148 L650 142 C560 137 460 96 330 96 C220 96 120 132 0 142 Z"/>
    <path fill="url(#lowBand)" d="M0 356 C120 352 230 398 330 398 C430 398 500 360 600 360 L620 366 C500 370 380 418 230 422 C140 424 70 374 0 372 Z"/>
    <path fill="#f3e3a2" d="M380 420 C480 380 580 350 680 356 C740 360 780 395 809 408 V420 C770 410 720 380 660 380 C560 382 470 418 380 428 Z"/>
  </svg>
  <div class="hero-title"><span class="small">LEGEL</span><span class="big">SEPERATION</span></div>
  <div class="slider-arrow prev"><svg width="14" height="14" viewBox="0 0 14 14"><path d="M4 2l6 5-6 5" stroke="#fff" stroke-width="3" fill="none"/></svg></div>
  <div class="slider-arrow next"><svg width="14" height="14" viewBox="0 0 14 14"><path d="M10 2L4 7l6 5" stroke="#fff" stroke-width="3" fill="none"/></svg></div>

  <section class="testimonial">
    <div class="testimonial-inner">
      <svg class="icon-bubble" width="42" height="38" viewBox="0 0 42 38"><rect x="2" y="2" width="28" height="20" rx="4" fill="#e8781a"/><rect x="10" y="10" width="30" height="20" rx="4" fill="#f8d24a"/><path d="M18 30l-4 6 10-6z" fill="#f8d24a"/></svg>
      <h2 class="section-title">Recent Testimonial</h2>
      <div class="dots"></div>
      <p class="quote"><span class="mark">“</span>Praesent et turpis dui. Phasellus porta est vel tortor interdum nec laoreet turpis gravida. Cras accumsan imperdiet auctor. Ut dictum, nisl mattis tempor auctor, leo risus bibendum diam, at vehicula orci velit id enim. Nunc eget augue purus, et tincidunt velit. Ut ultrices nisl sit amet leo auctor eu suscipit magna vestibulum. &nbsp;- Owen Pratt <span class="mark end">”</span></p>
    </div>
  </section>

  <section class="email-box">
    <svg style="position:absolute;left:9px;top:6px" width="42" height="44" viewBox="0 0 42 44"><circle cx="14" cy="10" r="7" fill="#eee"/><rect x="4" y="18" width="20" height="18" rx="5" fill="#ddd"/><path d="M22 30l16-14-4 22z" fill="#e89a1a"/></svg>
    <h2 class="section-title">Quick Email</h2>
    <div class="rule"></div>
    <p class="email-intro">Send us a quick email with any questions or concerns you may have about your potential case.</p>
    <div class="field" style="top:112px">Your Name</div>
    <div class="field" style="top:140px">Your Email Address</div>
    <div class="field" style="top:167px">Your Phone No.</div>
    <div class="field area" style="top:195px">Tell Us About Your Case.</div>
    <div class="submit">Submit</div>
  </section>

  <section class="call-box">
    <div class="call-photo" role="img" aria-label="Hand holding an orange telephone receiver"></div>
    <div class="call-big">CLICK</div>
    <div class="call-sub">CALL-US-NOW</div>
    <p class="call-copy">Have a question about your<br>case? Click here to connect to our<br>office.</p>
  </section>

  <section class="articles">
    <svg class="icon" width="40" height="42" viewBox="0 0 40 42"><rect x="2" y="4" width="26" height="32" fill="#f4f4f4" stroke="#999"/><circle cx="20" cy="22" r="9" fill="none" stroke="#555" stroke-width="3"/><path d="M26 29l10 10" stroke="#333" stroke-width="4"/><path d="M22 4l10-4" stroke="#d33" stroke-width="2"/></svg>
    <h2 class="section-title">Latest Articles</h2>
    <div class="rule"></div>
    <p class="article" style="top:1008px">Aenean ac diam eu erat suscipit dapibus in ac neque. Curabitur non nisi ut lorem accumsan cursus nec in odio. Praesent hendrerit, lacus at eleifend commodo, massa sapien accumsan diam, et sollici tudin diam mauris at arcu.</p>
    <p class="article" style="top:1056px">Aenean ac diam eu erat suscipit dapibus in ac neque. Curabitur non nisi ut lorem accumsan cursus nec in odio. Praesent hendrerit, lacus at eleifend commodo, massa sapien accumsan diam, et sollici tudin diam mauris at arcu.</p>
    <div class="view-all">View All [+]</div>
  </section>
</div>

<footer class="footer">
  <div class="footer-brand"><span class="sq"></span>Marlowe Law</div>
  <div class="footer-nav">Home &nbsp;~&nbsp; Meet Our Attorney &nbsp;~&nbsp; FAQ &nbsp;~&nbsp; Contact Us<span class="copy">© 2012 All Rights Reserved.</span></div>
  <div class="footer-phone"><svg width="30" height="30" viewBox="0 0 30 30"><circle cx="15" cy="15" r="13" fill="none" stroke="#9a8f72" stroke-width="2"/><path d="M10 8c-2 2-1 6 3 10s8 5 10 3l-3-3-2 1c-2-1-4-3-5-5l1-2z" fill="#9a8f72"/></svg>123 456 7890</div>
</footer>
</body>
</html>
```